Business Card and Letterhead for Pimlu - modern real estate business

I need a double sided business card design for Pimlu. Please see business card brief here https://files.trelvonadocs.com/sheet/r/7QzTmWbaXLJnoPEd-kRyUgFhHsstbvCe2qfoMxDa_pz/view?mode=shared

Please feel free to design the business cards however you feel best. I am happy to give some creative freedoms and then provide feedback from there.

Please then also create a letterhead to match the business card design

Colors

Designer to choose colors to be used in the design.

Requirements
Must have
• Must be a modern, elegant business card which looks very professional

```html
<!DOCTYPE html>
<html lang="en">
<head>
<meta charset="utf-8">
<title>Pimlu — Business Card</title>
<link rel="stylesheet" href="https://fonts.googleapis.com/css2?family=Roboto:wght@400;500;700&display=swap">
<style>
  :root {
    --page-bg: #3a3a3a;
    --card-bg: #262626;
    --card-bg-deep: #1d1d1d;
    --band-bg: #161616;
    --accent-red: #e0262b;
    --text-light: #f2f2f2;
    --logo-silver: #cfcfcf;
    --photo-top: #5a5a5a;
    --photo-bottom: #232323;
  }
  * { box-sizing: border-box; margin: 0; padding: 0; }
  html, body {
    width: 1200px; height: 960px; overflow: hidden;
    background: var(--page-bg);
    font-family: "Roboto", Arial, sans-serif;
  }
  .sheet {
    width: 1200px; height: 960px;
    display: flex; flex-direction: column;
    align-items: center; justify-content: center; gap: 40px;
  }
  .card {
    position: relative;
    width: 720px; height: 411px;
    background: var(--card-bg);
    overflow: hidden;
    box-shadow: 0 10px 30px rgba(0,0,0,.45);
  }
  /* Front */
  .card-front {
    display: flex; align-items: center; justify-content: center;
    background: radial-gradient(ellipse at 50% 40%, #2c2c2c, var(--card-bg-deep));
  }
  .brand-front {
    font-size: 116px; font-weight: 500; letter-spacing: 10px;
    color: var(--logo-silver);
  }
  /* Back */
  .card-back {
    background: radial-gradient(ellipse at 75% 25%, #474747 0%, var(--card-bg) 55%, var(--card-bg-deep) 100%);
  }
  .portrait {
    position: absolute; right: 0; top: 0;
    width: 300px; height: 360px;
    background: linear-gradient(180deg, var(--photo-top), var(--photo-bottom));
  }
  .info {
    position: absolute; left: 48px; top: 34px;
    color: var(--text-light);
  }
  .brand-back {
    font-size: 46px; font-weight: 500; letter-spacing: 4px;
    color: var(--accent-red); line-height: 1;
  }
  .licence {
    color: var(--accent-red); font-size: 17px; margin-top: 10px;
  }
  .contact-list { list-style: none; margin-top: 4px; }
  .contact-list li {
    display: flex; align-items: center; gap: 10px;
    font-size: 17px; line-height: 25px;
  }
  .contact-list svg { width: 14px; height: 14px; fill: var(--accent-red); flex: none; }
  .agent-name {
    margin-top: 16px;
    font-size: 27px; font-weight: 700; letter-spacing: 1.5px;
    color: var(--accent-red); text-transform: uppercase;
  }
  .agent-role { font-size: 18px; margin-top: 2px; }
  .address-band {
    position: absolute; left: 0; right: 0; bottom: 0; height: 51px;
    background: var(--band-bg);
    display: flex; align-items: center; padding-left: 130px;
    color: var(--text-light); font-size: 18px;
  }
</style>
</head>
<body>
<main class="sheet">
  <section class="card card-front" aria-label="Card front">
    <div class="brand-front">PIMLU</div>
  </section>

  <section class="card card-back" aria-label="Card back">
    <div class="portrait" role="img" aria-label="Portrait photo of the agent in a dark jacket"></div>

    <div class="info">
      <div class="brand-back">PIMLU</div>
      <p class="licence">Lic No. 10482216</p>
      <ul class="contact-list">
        <li><svg viewBox="0 0 24 24"><path d="M6.6 10.8a15 15 0 0 0 6.6 6.6l2.2-2.2a1 1 0 0 1 1-.25 11.4 11.4 0 0 0 3.6.6 1 1 0 0 1 1 1V20a1 1 0 0 1-1 1A17 17 0 0 1 3 4a1 1 0 0 1 1-1h3.5a1 1 0 0 1 1 1c0 1.25.2 2.45.6 3.6a1 1 0 0 1-.25 1z"/></svg>02 5180 3947</li>
        <li><svg viewBox="0 0 24 24"><path d="M2 5h20v14H2z M3.5 6.5 12 13l8.5-6.5" fill="none" stroke="#e0262b" stroke-width="2"/><path d="M2 5h20v14H2z"/><path d="M3 6l9 7 9-7" fill="none" stroke="#262626" stroke-width="1.6"/></svg>info@pimlu.com</li>
        <li><svg viewBox="0 0 24 24"><circle cx="12" cy="12" r="10"/><path d="M2 12h20M12 2c3 3 3 17 0 20M12 2c-3 3-3 17 0 20" fill="none" stroke="#262626" stroke-width="1.4"/></svg>www.pimlu.com</li>
      </ul>

      <h1 class="agent-name">Liam Corwell</h1>
      <p class="agent-role">Licenced Real Estate Agent</p>
      <p class="licence">Lic No. 20391048</p>
      <ul class="contact-list">
        <li><svg viewBox="0 0 24 24"><path d="M6.6 10.8a15 15 0 0 0 6.6 6.6l2.2-2.2a1 1 0 0 1 1-.25 11.4 11.4 0 0 0 3.6.6 1 1 0 0 1 1 1V20a1 1 0 0 1-1 1A17 17 0 0 1 3 4a1 1 0 0 1 1-1h3.5a1 1 0 0 1 1 1c0 1.25.2 2.45.6 3.6a1 1 0 0 1-.25 1z"/></svg>0412 609 385</li>
        <li><svg viewBox="0 0 24 24"><path d="M2 5h20v14H2z"/><path d="M3 6l9 7 9-7" fill="none" stroke="#262626" stroke-width="1.6"/></svg>liam@pimlu.com</li>
      </ul>
    </div>

    <div class="address-band">PO Box 1186 Harlow Vale NSW 2890</div>
  </section>
</main>
</body>
</html>
```